Brell Stone Company Business Cards

Front and Back Business Card - logo and text setup - cool design. I need workable photoshop or illustrator files so I can setup each employee card with design that is created
Updates

Hi everyone, thank you for the great entries. Please no more white and blue cards - there are so many already - black and silver only now please. thanks!

Target Market(s)

Construction Industry - Facility Managers

Industry/Entity Type

Construction

Contact Information for Business Card

I really like contemporary simplistic looks - clean neat....not opposed to seeing some black backrounds

Requirements
Must have
• Logo/website address with design on front only - www.brellstone-example.com (logo attached)
• Back:
• Name/Title/Company Address/Phone/email address
Nice to have
• Cool design
Should not have
• Nothing gimmicky like Fire or Water - since we are a Fire Protection company - it has all been done

```html
<!DOCTYPE html>
<html lang="en">
<head>
<meta charset="utf-8">
<title>Brell Stone Company – Business Cards</title>
<link rel="stylesheet" href="https://fonts.googleapis.com/css2?family=Lato:wght@400;900&display=swap">
<style>
  :root {
    --black: #131315;
    --silver: #c3c6cb;
    --silver-light: #e2e4e7;
    --silver-dark: #8d9197;
    --stage: #2c2c2f;
    --card-w: 600px;
    --card-h: 343px;
  }
  * { margin: 0; padding: 0; box-sizing: border-box; }
  html, body { width: 1200px; height: 912px; overflow: hidden; }
  body {
    background: var(--stage);
    font-family: "Lato", sans-serif;
    display: flex;
    flex-direction: column;
    align-items: center;
    justify-content: center;
    gap: 60px;
  }
  .card {
    position: relative;
    width: var(--card-w);
    height: var(--card-h);
    overflow: hidden;
    background: var(--black);
  }

  /* Wordmark */
  .wordmark {
    display: flex;
    align-items: center;
    gap: 14px;
    font-weight: 900;
    font-size: 58px;
    letter-spacing: -1px;
    line-height: 1;
    white-space: nowrap;
  }
  .wordmark-square {
    width: 22px;
    height: 22px;
    flex: none;
  }

  /* Front */
  .card-front .wordmark {
    position: absolute;
    left: 50%;
    top: 130px;
    transform: translateX(-50%);
    color: var(--silver-light);
  }
  .card-front .wordmark-square { background: var(--silver-dark); }
  .card-front .front-url {
    position: absolute;
    left: 0; right: 0;
    bottom: 62px;
    text-align: center;
    color: var(--silver);
    font-size: 15px;
    letter-spacing: 0.5px;
  }

  /* Back */
  .back-shape { position: absolute; inset: 0; }
  .card-back .wordmark {
    position: absolute;
    left: 38px;
    top: 104px;
    color: var(--black);
    font-size: 50px;
  }
  .card-back .wordmark-square { background: var(--silver-dark); }
  .contact-block {
    position: absolute;
    right: 30px;
    top: 168px;
    text-align: right;
    color: var(--silver-light);
  }
  .person-name {
    color: var(--silver);
    font-size: 22px;
    line-height: 1.1;
  }
  .person-title {
    font-size: 14px;
    margin: 2px 0 12px;
  }
  .contact-line {
    display: flex;
    justify-content: flex-end;
    align-items: center;
    gap: 6px;
    font-size: 13px;
    line-height: 1.55;
  }
  .contact-line svg { width: 11px; height: 11px; flex: none; }
  .icon-fill { fill: var(--silver); }
  .icon-stroke { fill: none; stroke: var(--silver); stroke-width: 2.4; stroke-linejoin: round; }
  .address {
    position: absolute;
    left: 36px;
    bottom: 22px;
    color: var(--silver-light);
    font-size: 17px;
    line-height: 1.25;
  }
</style>
</head>
<body>

  <section class="card card-front" aria-label="Card front">
    <div class="wordmark"><span class="wordmark-square"></span>Brell Stone</div>
    <p class="front-url">www.brellstone-example.com</p>
  </section>

  <section class="card card-back" aria-label="Card back">
    <svg class="back-shape" viewBox="0 0 600 343" width="600" height="343" aria-hidden="true">
      <defs>
        <linearGradient id="silver-panel" x1="0" y1="0" x2="1" y2="1">
          <stop offset="0" stop-color="#eceef0"/>
          <stop offset="1" stop-color="#c3c6cb"/>
        </linearGradient>
      </defs>
      <rect width="600" height="343" fill="var(--black)"/>
      <path d="M0 0 H372 C398 120 320 232 0 262 Z" fill="url(#silver-panel)"/>
      <path d="M384 0 C410 80 395 150 322 212" fill="none" stroke="var(--silver)" stroke-width="4" stroke-linecap="round"/>
    </svg>

    <div class="wordmark"><span class="wordmark-square"></span>Brell Stone</div>

    <div class="contact-block">
      <p class="person-name">Dana Whitlow Marsh</p>
      <p class="person-title">President</p>
      <p class="contact-line">(555) 014-2290
        <svg viewBox="0 0 24 24"><path class="icon-fill" d="M6.6 10.8a15 15 0 0 0 6.6 6.6l2.2-2.2a1 1 0 0 1 1-.25 11.4 11.4 0 0 0 3.6.57 1 1 0 0 1 1 1V20a1 1 0 0 1-1 1A17 17 0 0 1 3 4a1 1 0 0 1 1-1h3.5a1 1 0 0 1 1 1c0 1.25.2 2.45.57 3.57a1 1 0 0 1-.25 1z"/></svg>
      </p>
      <p class="contact-line">info@brellstone-example.com
        <svg viewBox="0 0 24 24"><path class="icon-stroke" d="M2 5h20v14H2z M2 5l10 8 10-8"/></svg>
      </p>
      <p class="contact-line">www.brellstone-example.com
        <svg viewBox="0 0 24 24"><circle class="icon-fill" cx="12" cy="12" r="10"/></svg>
      </p>
    </div>

    <p class="address">40 Harbor Park Lane<br>Millbrook, NY 10000</p>
  </section>

</body>
</html>
```